Card design for orthopaedic surgeons working as The Brightwater Joint Centre

Business cards, letterhead

Colors

Designer to choose colors to be used in the design.

Requirements
Must have
• Late addition.
• Cards letterhead must have logos of
• Crestmoor Lindell College of Surgeons
• Varenwood Bone Health Association
Nice to have
• Back of card to have space for appointment time to be added by hand and some blank space for writing incidental other notes.

```html
<!DOCTYPE html>
<html lang="en">
<head>
<meta charset="utf-8">
<title>The Brightwater Joint Centre – Stationery</title>
<link href="https://fonts.googleapis.com/css2?family=Nunito+Sans:wght@400;600;700&family=Arimo:wght@400;700&family=Caveat:wght@400&display=swap" rel="stylesheet">
<style>
  :root{
    --navy:#0d344d;
    --sky:#5aa0d4;
    --paper:#f5f5f5;
    --ink:#1e1e1e;
    --backdrop:#e3e3e3;
    --badge-warm:#b9894f;
    --badge-cool:#8e9aa8;
  }
  html,body{margin:0;padding:0;width:1200px;height:1200px;overflow:hidden;}
  body{background:radial-gradient(circle at 55% 50%, #ececec 0%, var(--backdrop) 70%, #d8d8d8 100%);}
  .stage{position:absolute;left:0;top:0;width:1932px;height:1932px;transform:scale(0.621118);transform-origin:0 0;}
  .sheet{position:absolute;background:var(--paper);box-shadow:2px 3px 6px rgba(0,0,0,.35);overflow:hidden;}
  .sheet svg.waves{position:absolute;left:0;top:0;}
  .brand-name{position:absolute;font-family:"Nunito Sans",sans-serif;font-weight:400;color:var(--navy);white-space:nowrap;letter-spacing:-.5px;}
  .contact{position:absolute;font-family:"Nunito Sans",sans-serif;color:#fff;text-align:right;}
  .contact p{margin:0;}
  .contact .ico{display:inline-block;vertical-align:middle;margin-left:5px;}
  .badge{position:absolute;}

  /* Letterhead */
  .letterhead{left:158px;top:199px;width:1090px;height:1540px;}
  .letterhead .brand-name{left:76px;top:120px;font-size:34px;}
  .letterhead .contact{right:53px;top:28px;font-size:17px;line-height:20.5px;letter-spacing:.4px;}
  .letterhead .contact .gap{margin-top:6px;}
  .letter{position:absolute;left:76px;top:355px;width:937px;font-family:Arimo,sans-serif;font-size:16px;line-height:22px;color:var(--ink);}
  .letter p{margin:0;}
  .letter .date{margin-bottom:22px;}
  .letter .salutation{font-weight:700;margin-top:48px;margin-bottom:44px;}
  .letter .body p{text-align:justify;margin-bottom:22px;}
  .letter .closing{margin-top:52px;}
  .letter .signature{font-family:Caveat,cursive;font-size:38px;line-height:40px;margin:26px 0 22px;}

  /* Cards */
  .card{width:467px;height:285px;left:1326px;}
  .appointment{top:446px;}
  .appointment h2{position:absolute;left:32px;top:40px;margin:0;font-family:"Nunito Sans",sans-serif;font-weight:700;font-size:16px;color:var(--sky);}
  .field{position:absolute;left:32px;right:36px;height:20px;font-family:"Nunito Sans",sans-serif;font-size:12.5px;color:var(--navy);}
  .field .rule{position:absolute;left:42px;right:0;bottom:3px;border-bottom:1px solid var(--sky);}
  .field .sub{position:absolute;left:254px;top:0;}
  .appointment .site{position:absolute;left:0;right:0;top:243px;text-align:center;font-family:"Nunito Sans",sans-serif;font-size:13px;color:var(--navy);}

  .profile{top:813px;}
  .profile .brand-name{left:32px;top:48px;font-size:18.5px;}
  .holder{position:absolute;left:32px;top:136px;font-family:"Nunito Sans",sans-serif;}
  .holder .name{margin:0;font-weight:700;font-size:16px;color:var(--sky);}
  .holder .role{margin:0;font-size:13px;color:var(--navy);}
  .profile .contact{right:27px;top:177px;font-size:12.5px;line-height:15.5px;}
  .profile .contact .gap{margin-top:5px;}
</style>
</head>
<body>
<div class="stage">

  <!-- Letterhead -->
  <section class="sheet letterhead">
    <svg class="waves" width="1090" height="210" viewBox="0 0 1090 210" aria-hidden="true">
      <path d="M0,0 H1090 V195 C880,200 690,135 500,92 C330,52 150,42 0,80 Z" fill="var(--sky)"/>
      <path d="M0,0 H1090 V152 C880,178 690,115 490,68 C330,30 140,10 0,42 Z" fill="var(--navy)"/>
      <path d="M0,76 C150,36 320,34 490,68" fill="none" stroke="var(--navy)" stroke-width="6"/>
    </svg>
    <div class="brand-name">The Brightwater Joint Centre</div>
    <div class="contact">
      <p>48 Harbour Row</p>
      <p>Eastvale, Florida, 33190</p>
      <p class="gap">(555) 014-2290<svg class="ico" width="13" height="13" viewBox="0 0 16 16"><path d="M3,1 L6,1 L7,5 L5,6.5 C6,9 7,10 9.5,11 L11,9 L15,10 L15,13 C15,14 14,15 13,15 C6,15 1,10 1,3 C1,2 2,1 3,1 Z" fill="var(--sky)"/></svg></p>
      <p>daniel@brightwaterjoint.com<svg class="ico" width="14" height="11" viewBox="0 0 16 12"><rect x="1" y="1" width="14" height="10" fill="none" stroke="var(--sky)" stroke-width="1.5"/><path d="M1,1 L8,7 L15,1" fill="none" stroke="var(--sky)" stroke-width="1.5"/></svg></p>
      <p>www.brightwaterjoint.com<svg class="ico" width="13" height="13" viewBox="0 0 16 16"><circle cx="8" cy="8" r="6.5" fill="none" stroke="var(--sky)" stroke-width="1.3"/><ellipse cx="8" cy="8" rx="3" ry="6.5" fill="none" stroke="var(--sky)" stroke-width="1.1"/><path d="M1.5,8 H14.5" stroke="var(--sky)" stroke-width="1.1"/></svg></p>
    </div>

    <div class="letter">
      <p class="date">November 12, 2019</p>
      <p>Mr. Peter Lane<br>President<br>Northfield Group<br>111 Street Name, Suite#<br>City, State, 12345</p>
      <p class="salutation">Dear Mr. Lane,</p>
      <div class="body">
        <p>Lorem ipsum dolor sit amet, consectetur adipiscing elit. Integer diam quam, egestas eu ultrices eu, suscipit ac sapien. Phasellus eu dui nisi. Nam et euismod diam, nec lobortis tortor. Donec et diam nulla. Aenean varius tincidunt convallis. Aliquam a tortor at lacus dictum aliquet. Nunc laoreet metus sapien, in scelerisque augue consectetur in.</p>
        <p>Fusce nec justo laoreet, egestas justo sed, aliquet sem. Pellentesque pharetra massa non orci bibendum semper. Pellentesque cursus eu lectus a consectetur. Nunc volutpat suscipit posuere. Vestibulum facilisis vel quam malesuada mattis. Nulla in mattis tellus. Maecenas tristique mauris vitae pharetra tincidunt. In ut ornare risus. Integer molestie vestibulum nisi, semper dapibus mi condimentum eu.</p>
        <p>Nullam sagittis elit libero, id fringilla est tincidunt eget. Donec in ipsum ultricies, consectetur quam vel, facilisis elit. Phasellus tincidunt congue risus vel luctus. Suspendisse ut mollis neque. Donec ornare orci in turpis vestibulum, in ultrices metus scelerisque. Pellentesque mattis mattis nunc, nec tincidunt lacus egestas id. Fusce facilisis sagittis neque sit amet vulputate. Aliquam ut eros lobortis tortor facilisis vehicula. Sed sed luctus leo, at laoreet sapien. Donec placerat adipiscing ligula non euismod. In lobortis pretium nisl id luctus.</p>
        <p>Integer gravida tincidunt nibh, scelerisque tincidunt turpis. Suspendisse potenti. Nunc hendrerit euismod lectus id elementum. Fusce vitae gravida velit, quis eleifend lectus. In imperdiet mauris eu dui viverra sagittis. Donec tempor dui diam, condimentum gravida lacus pretium a. Nullam fringilla augue quis arcu placerat scelerisque. Aliquam nec tincidunt augue, sit amet posuere ipsum.</p>
      </div>
      <p class="closing">Sincerely Yours,</p>
      <p class="signature">Daniel Hartley</p>
      <p>Daniel Hartley<br>Managing Director</p>
    </div>

    <svg class="badge" style="left:782px;top:1381px" width="90" height="110" viewBox="0 0 90 110" role="img" aria-label="Crestmoor Lindell College of Surgeons badge">
      <rect x="0" y="0" width="90" height="110" rx="8" fill="var(--badge-warm)" opacity=".75"/>
    </svg>
    <svg class="badge" style="left:905px;top:1388px" width="110" height="103" viewBox="0 0 110 103" role="img" aria-label="Varenwood Bone Health Association badge">
      <rect x="0" y="0" width="110" height="103" rx="8" fill="var(--badge-cool)" opacity=".75"/>
    </svg>
  </section>

  <!-- Appointment card -->
  <section class="sheet card appointment">
    <svg class="waves" width="467" height="120" viewBox="0 0 467 120" aria-hidden="true">
      <path d="M0,0 H467 V30 C380,18 320,42 240,80 C160,116 80,120 0,114 Z" fill="var(--sky)"/>
      <path d="M0,0 H467 V4 C380,-2 310,30 235,62 C160,94 80,100 0,90 Z" fill="var(--navy)"/>
      <path d="M275,36 C340,8 400,4 467,14" fill="none" stroke="var(--navy)" stroke-width="4"/>
    </svg>
    <h2>Next Appointment</h2>
    <div class="field" style="top:128px">Name<span class="rule"></span></div>
    <div class="field" style="top:170px">Date<span class="rule"></span><span class="sub">Time</span></div>
    <div class="field" style="top:212px">Note<span class="rule"></span></div>
    <div class="site">www.brightwaterjoint.com</div>
  </section>

  <!-- Profile card -->
  <section class="sheet card profile">
    <svg class="waves" width="467" height="285" viewBox="0 0 467 285" aria-hidden="true">
      <path d="M0,222 C90,250 180,220 270,180 C350,145 410,130 467,133 V285 H0 Z" fill="var(--sky)"/>
      <path d="M0,245 C110,262 200,228 290,190 C360,162 420,150 467,154 V285 H0 Z" fill="var(--navy)"/>
      <path d="M0,232 C60,244 130,240 190,218" fill="none" stroke="var(--navy)" stroke-width="4"/>
    </svg>
    <div class="brand-name">The Brightwater Joint Centre</div>
    <svg class="badge" style="left:320px;top:30px" width="48" height="58" viewBox="0 0 48 58" role="img" aria-label="Crestmoor Lindell College of Surgeons badge">
      <rect x="0" y="0" width="48" height="58" rx="5" fill="var(--badge-warm)" opacity=".75"/>
    </svg>
    <svg class="badge" style="left:382px;top:33px" width="58" height="54" viewBox="0 0 58 54" role="img" aria-label="Varenwood Bone Health Association badge">
      <rect x="0" y="0" width="58" height="54" rx="5" fill="var(--badge-cool)" opacity=".75"/>
    </svg>
    <div class="holder">
      <p class="name">Daniel Hartley</p>
      <p class="role">Managing Director</p>
    </div>
    <div class="contact">
      <p>48 Harbour Row</p>
      <p>Eastvale, Florida, 33190</p>
      <p class="gap">(555) 014-2290<svg class="ico" width="10" height="10" viewBox="0 0 16 16"><path d="M3,1 L6,1 L7,5 L5,6.5 C6,9 7,10 9.5,11 L11,9 L15,10 L15,13 C15,14 14,15 13,15 C6,15 1,10 1,3 C1,2 2,1 3,1 Z" fill="var(--sky)"/></svg></p>
      <p>daniel@brightwaterjoint.com<svg class="ico" width="11" height="8" viewBox="0 0 16 12"><rect x="1" y="1" width="14" height="10" fill="none" stroke="var(--sky)" stroke-width="1.5"/><path d="M1,1 L8,7 L15,1" fill="none" stroke="var(--sky)" stroke-width="1.5"/></svg></p>
      <p>www.brightwaterjoint.com<svg class="ico" width="10" height="10" viewBox="0 0 16 16"><circle cx="8" cy="8" r="6.5" fill="none" stroke="var(--sky)" stroke-width="1.3"/><ellipse cx="8" cy="8" rx="3" ry="6.5" fill="none" stroke="var(--sky)" stroke-width="1.1"/><path d="M1.5,8 H14.5" stroke="var(--sky)" stroke-width="1.1"/></svg></p>
    </div>
  </section>

</div>
</body>
</html>
```